Business Cards for new orthopaedic surgery practice

My husband and I are starting our own orthopaedic surgery practice. We are looking for a business card that is uniform, but one will have my name/title and the other will have his. You can just create one design with my name on it for now. But when I choose your design as the winning design I will ask that you add another copy with his name/title.

We are looking for classy, simple, elite all in one. We like dark blues/a little gold/yellow. Something that goes with our logo. We want our logo incorporated. Here is all the info you need:
Business name: RV Bone & Vitality Center
Location: 38517 North Willowmere Ave
Briarton Springs, FL 33482
Phone: 954-218-4063
Fax: 954-582-7341
Email: info@myrvbonecare.example

Names: Lydia Vance, M.D.
Board Certified Hand and Upper Extremity Surgeon

Ebo Dansu, M.D.
Board Certified Hip & Knee Replacement/General Orthopaedic Surgeon

Can decide what you want to put on the back. Maybe a slogan:
Steady Hands. Stronger Lives Ahead

I am just going to upload our logo. The only thing is if we select you as the winning design, the location, and phone numbers may change. We will need your help to update that once fully solidified.

Industry/Entity Type

Medical

Contact Information for Business Card

Colors
0054AA
0677BA
7BADD7
CADEEF
E8F1F8
0094D4
00A9DD
6FCCEA
C7EBF8
E9F6FB

Requirements
Must have
• class, appeal,
Should not have
• We want to air on the side of masculine if we are looking at masculine vs. feminine feel. But we still want it classy, sophisticated, and something we will love

```html
<!DOCTYPE html>
<html lang="en">
<head>
<meta charset="utf-8">
<title>RV Bone &amp; Vitality Center — Business Cards</title>
<link href="https://fonts.googleapis.com/css2?family=Cinzel:wght@400;600&family=Crimson+Text:wght@400;600&display=swap" rel="stylesheet">
<style>
  :root {
    --backdrop: #3a3a3c;
    --navy: #1f3a8a;
    --cyan: #17b9e0;
    --sky: #1aa9dd;
    --paper: #f6f9fb;
    --ink: #1f3a8a;
  }
  * { box-sizing: border-box; margin: 0; padding: 0; }
  html, body { width: 1200px; height: 694px; overflow: hidden; }
  body {
    background: var(--backdrop);
    font-family: "Crimson Text", Georgia, serif;
    position: relative;
  }
  .card {
    position: absolute;
    width: 520px;
    height: 297px;
    box-shadow: 0 18px 40px rgba(0,0,0,.45);
    overflow: hidden;
  }

  /* Front */
  .card-front {
    left: 50px; top: 50px;
    background: var(--cyan);
  }
  .card-front .edge-band {
    position: absolute; left: 0; right: 0; bottom: 0; height: 8px;
    background: var(--navy);
  }
  .front-name {
    position: absolute; left: 0; right: 0; top: 104px;
    text-align: center;
    font-family: "Cinzel", Georgia, serif;
    font-weight: 600;
    font-size: 30px;
    line-height: 1.15;
    color: var(--navy);
    letter-spacing: .5px;
  }
  .front-name .mark {
    display: inline-block; width: 14px; height: 14px; border-radius: 50%;
    background: var(--navy); margin-right: 10px; vertical-align: middle;
  }
  .slogan {
    position: absolute; left: 0; right: 0; bottom: 36px;
    text-align: center;
    font-family: "Cinzel", Georgia, serif;
    font-size: 11px;
    letter-spacing: 3px;
    color: var(--navy);
  }

  /* Back */
  .card-back {
    left: 630px; top: 340px;
    background: var(--paper);
  }
  .card-back .side-band {
    position: absolute; left: 0; top: 40px; width: 7px; height: 210px;
    background: var(--navy);
  }
  .card-back .edge-band {
    position: absolute; right: 0; bottom: 0; width: 290px; height: 7px;
    background: var(--navy);
  }
  .back-brand {
    position: absolute; right: 28px; top: 26px;
    font-family: "Crimson Text", Georgia, serif;
    font-weight: 600;
    font-size: 19px;
    color: var(--navy);
    display: flex; align-items: center; gap: 8px;
  }
  .back-brand .mark {
    width: 10px; height: 10px; border-radius: 50%; background: var(--navy);
  }
  .person {
    position: absolute; left: 32px; top: 84px;
  }
  .person-name {
    font-size: 20px; letter-spacing: .5px;
    color: var(--sky); text-transform: uppercase;
  }
  .person-title {
    font-size: 13px; line-height: 1.2; color: var(--ink); margin-top: 2px;
  }
  .contact {
    position: absolute; right: 28px; top: 72px;
    text-align: right;
    font-size: 12.5px; line-height: 1.35; color: var(--ink);
  }
  .contact .row { display: flex; justify-content: flex-end; align-items: center; gap: 6px; }
  .contact svg { width: 10px; height: 10px; fill: var(--sky); }
  .contact .address { margin-bottom: 6px; }
  .appointment {
    position: absolute; left: 32px; top: 182px; width: 280px;
  }
  .appointment-title {
    font-size: 13px; color: var(--sky); text-transform: uppercase; letter-spacing: .5px;
    margin-bottom: 8px;
  }
  .field {
    display: flex; align-items: flex-end; gap: 8px;
    font-size: 13px; color: var(--ink); height: 22px;
  }
  .field .label { width: 38px; }
  .field .line { flex: 1; border-bottom: 2px dotted var(--navy); margin-bottom: 5px; }
</style>
</head>
<body>
  <section class="card card-front" aria-label="Card front">
    <h1 class="front-name"><span class="mark"></span>RV Bone &amp;<br>Vitality Center</h1>
    <p class="slogan">STEADY HANDS. STRONGER LIVES AHEAD</p>
    <div class="edge-band"></div>
  </section>

  <section class="card card-back" aria-label="Card back">
    <div class="side-band"></div>
    <div class="back-brand"><span class="mark"></span>RV Bone &amp; Vitality Center</div>

    <div class="person">
      <h2 class="person-name">Lydia Vance, M.D.</h2>
      <p class="person-title">Board Certified Hand<br>and Upper Extremity Surgeon</p>
    </div>

    <div class="contact">
      <p class="address">38517 North Willowmere Ave<br>Briarton Springs, FL 33482</p>
      <p class="row">954-218-4063
        <svg viewBox="0 0 10 10" aria-hidden="true"><path d="M2 0.5l2 2-1 1.2c.6 1.3 1.6 2.3 2.9 2.9l1.2-1 2 2-1.3 1.9C4.4 9.2.8 5.6.5 1.8z"/></svg>
      </p>
      <p class="row">954-582-7341
        <svg viewBox="0 0 10 10" aria-hidden="true"><rect x="2" y="0.5" width="6" height="3"/><rect x="0.5" y="3.5" width="9" height="4.5" rx="1"/><rect x="2.5" y="6.5" width="5" height="3"/></svg>
      </p>
      <p class="row">info@myrvbonecare.example
        <svg viewBox="0 0 10 10" aria-hidden="true"><rect x="0.5" y="1.5" width="9" height="7" rx="1"/><path d="M1 2l4 3.3L9 2" stroke="#fff" stroke-width="1" fill="none"/></svg>
      </p>
    </div>

    <div class="appointment">
      <p class="appointment-title">Appointment with us</p>
      <div class="field"><span class="label">Date</span><span class="line"></span></div>
      <div class="field"><span class="label">Time</span><span class="line"></span></div>
      <div class="field"><span class="label">Place</span><span class="line"></span></div>
    </div>
    <div class="edge-band"></div>
  </section>
</body>
</html>
```